Business card design

I need my logo on this card, things I need the card to have on it
licensed and insured.
owner operators Milo & Trent Halvorsen
my phone number 5083716254
Disaster Recovery, Storm Damage Restoration, Proactive Disaster Plan Management, Roof Repair/Restoration Structural Repair and Reconstruction, Emergency Boarding and Tarping Service, Perimeter Fencing, Emergency Tree Removal,

```html
<!DOCTYPE html>
<html lang="en">
<head>
<meta charset="utf-8">
<title>Halvorsen's Construction – Business Card</title>
<link rel="stylesheet" href="https://fonts.googleapis.com/css2?family=Quicksand:wght@500;600&display=swap">
<style>
  :root {
    --backdrop: #a3a3a3;
    --card-dark: #121212;
    --card-light: #ffffff;
    --brand-blue: #3a8fd6;
    --text-light: #f2f2f2;
    --text-dark: #1d1d1d;
  }
  * { box-sizing: border-box; margin: 0; padding: 0; }
  html, body {
    width: 1093px; height: 1200px; overflow: hidden;
    background: var(--backdrop);
    font-family: "Quicksand", sans-serif;
  }
  .canvas { position: relative; width: 1093px; height: 1200px; }
  .card {
    position: absolute; left: 263px; width: 582px; height: 362px;
    border-radius: 20px; overflow: hidden;
  }
  .card--front { top: 224px; background: var(--card-dark); }
  .card--back { top: 619px; background: var(--card-light); }

  .brand {
    position: absolute; left: 44px; width: 220px;
    display: flex; flex-direction: column; align-items: center;
    text-align: center;
  }
  .card--front .brand { top: 118px; }
  .card--back .brand { top: 134px; }
  .brand__mark { width: 52px; height: 52px; background: var(--brand-blue); margin-bottom: 14px; }
  .brand__name {
    font-size: 20px; font-weight: 500; line-height: 24px;
    color: var(--brand-blue);
  }

  .divider { position: absolute; width: 1.5px; background: var(--brand-blue); }
  .card--front .divider { left: 274px; top: 91px; height: 179px; }
  .card--back .divider { left: 285px; top: 106px; height: 173px; }

  .services {
    position: absolute; left: 285px; top: 87px; list-style: none;
    color: var(--text-light); font-size: 14px; font-weight: 500;
  }
  .services li {
    position: relative; padding-left: 12px; line-height: 16px; margin-bottom: 9.2px;
  }
  .services li::before {
    content: ""; position: absolute; left: 0; top: 5px;
    width: 7px; height: 7px; border-radius: 50%; background: var(--brand-blue);
  }

  .contact { position: absolute; left: 298px; top: 104px; color: var(--text-dark); }
  .contact__name { font-size: 22px; font-weight: 500; color: var(--brand-blue); line-height: 28px; }
  .contact__role { font-size: 13px; font-weight: 600; margin-top: 1px; line-height: 16px; }
  .contact__address { font-size: 13.5px; font-weight: 500; line-height: 16px; margin-top: 14px; }
  .contact__lines { list-style: none; margin-top: 12px; font-size: 13.5px; font-weight: 600; }
  .contact__lines li { display: flex; align-items: center; height: 23px; }
  .contact__lines svg { width: 15px; height: 15px; margin-right: 9px; fill: var(--brand-blue); }
</style>
</head>
<body>
<div class="canvas">

  <section class="card card--front">
    <div class="brand">
      <div class="brand__mark"></div>
      <div class="brand__name">Halvorsen's Construction L.L.C</div>
    </div>
    <div class="divider"></div>
    <ul class="services">
      <li>Disaster Recovery</li>
      <li>Storm Damage Restoration</li>
      <li>Proactive Disaster Plan Management</li>
      <li>Perimeter Fencing</li>
      <li>Emergency Boarding and Tarping Service</li>
      <li>Emergency Tree Removal</li>
      <li>Roof Repair/Restoration Structural Repai<br>And Reconstruction</li>
    </ul>
  </section>

  <section class="card card--back">
    <div class="brand">
      <div class="brand__mark"></div>
      <div class="brand__name">Halvorsen's Construction L.L.C</div>
    </div>
    <div class="divider"></div>
    <div class="contact">
      <div class="contact__name">Milo &amp; Trent Halvorsen</div>
      <div class="contact__role">owner operators</div>
      <div class="contact__role">licensed and insured</div>
      <div class="contact__address">48 Birch Hollow Lane<br>Dalton, MS 39207</div>
      <ul class="contact__lines">
        <li>
          <svg viewBox="0 0 16 16" aria-hidden="true"><path d="M1 6c0-2 3-3.5 7-3.5S15 4 15 6v1.5h-3.5V6h-7v1.5H1z"/><path d="M4 8h8l2 5H2z"/><circle cx="8" cy="10.5" r="1.3" fill="#fff"/></svg>
          &nbsp;5083716254
        </li>
        <li>
          <svg viewBox="0 0 16 16" aria-hidden="true"><path d="M1 3h14v10H1z"/><path d="M1.5 3.5L8 9l6.5-5.5" stroke="#fff" stroke-width="1.3" fill="none"/></svg>
          info@halvorsenbuild.com
        </li>
        <li>
          <svg viewBox="0 0 16 16" aria-hidden="true"><circle cx="8" cy="8" r="7"/><path d="M3 5.5c2 0 2 2 3.5 2.5S7 11 6 13M10 2.5c-1 2 1 3 3 3M11 9c1 1 1 3 0 4" stroke="#fff" stroke-width="1.2" fill="none"/></svg>
          www.halvorsenbuild.com
        </li>
      </ul>
    </div>
  </section>

</div>
</body>
</html>
```